Business Card Design Project

I require a business card with the following information on them for various different people;
name
m:
f:
e:
I have a logo already and will attached that. We are in the construction industry. I require something clean and simple but eye catching at the same time. You can use another colour with our logo if you like and you can style the logo as well if you wish. I am open.
Also it needs to be front and back design.
Industry/Entity Type
Construction
Requirements
Must have
- Logo, name, mobile, fax and email address.
Front and back design

```html
<!DOCTYPE html>
<html lang="en">
<head>
<meta charset="utf-8">
<title>Northgate Developments – Business Card Front and Back</title>
<link href="https://fonts.googleapis.com/css2?family=Questrial&family=Arimo&display=swap" rel="stylesheet">
<style>
  :root{
    --page:#ffffff;
    --card-white:#ffffff;
    --card-border:#9a9a9a;
    --brand-green:#3aa335;
    --green-light:#a6d85a;
    --green-dark:#4ea82a;
    --brand-blue:#3771e8;
    --blue-pale:#a9c2f3;
    --panel-grey:#e8e8e8;
    --ink:#111111;
    --white:#ffffff;
  }
  html,body{margin:0;padding:0;overflow:hidden;}
  body{width:1200px;height:900px;background:var(--page);position:relative;}
  .card{position:absolute;top:270px;width:495px;height:283px;border-radius:14px;overflow:hidden;
        box-shadow:2px 3px 4px rgba(0,0,0,.35);}
  .card svg{display:block;}
  .card--front{left:82px;background:var(--card-white);box-shadow:2px 3px 4px rgba(0,0,0,.35), inset 0 0 0 1px var(--card-border);}
  .card--back{left:628px;background:var(--brand-blue);}
  .wordmark{font-family:"Questrial",sans-serif;}
  .contact{font-family:"Arimo",sans-serif;fill:var(--ink);}
</style>
</head>
<body>

<section class="card card--front" aria-label="Business card front">
  <svg width="495" height="283" viewBox="0 0 495 283">
    <defs>
      <linearGradient id="tabBlue" x1="0" y1="0" x2="0" y2="1">
        <stop offset="0" stop-color="#3771e8"/>
        <stop offset=".5" stop-color="#a9c2f3"/>
        <stop offset="1" stop-color="#3771e8"/>
      </linearGradient>
      <linearGradient id="panelGreen" x1="0" y1="0" x2="1" y2="1">
        <stop offset="0" stop-color="#a6d85a"/>
        <stop offset=".7" stop-color="#5fb22c"/>
        <stop offset="1" stop-color="#4ea82a"/>
      </linearGradient>
    </defs>
    <rect class="side-tab" x="-6" y="48" width="20" height="185" rx="8" fill="url(#tabBlue)"/>
    <rect class="side-tab" x="481" y="48" width="20" height="185" rx="8" fill="url(#tabBlue)"/>

    <g class="brand">
      <rect x="92" y="112" width="50" height="50" rx="3" fill="var(--brand-green)"/>
      <text class="wordmark" x="156" y="147" font-size="44" fill="var(--brand-green)">Northgate</text>
      <text class="wordmark" x="158" y="163" font-size="13" letter-spacing="5.2" fill="var(--brand-green)">DEVELOPMENTS</text>
    </g>

    <path class="contact-panel" d="M58 283 L126 208 Q133 200 145 200 L428 200 Q438 200 438 210 L438 283 Z" fill="url(#panelGreen)"/>
    <g class="contact">
      <text x="191" y="218" font-size="14.5">name xxxxxxx.......</text>
      <text x="201" y="235" font-size="11.5">m : xxxxxxxxxxxx</text>
      <text x="201" y="252" font-size="11.5">f&#160;&#160;: xxxxxxxxxxxx</text>
      <text x="201" y="269" font-size="11.5">e&#160;&#160;: xxxxxxx@xxxx.com</text>
    </g>
  </svg>
</section>

<section class="card card--back" aria-label="Business card back">
  <svg width="495" height="283" viewBox="0 0 495 283">
    <rect class="side-tab" x="-6" y="48" width="20" height="185" rx="8" fill="var(--panel-grey)"/>
    <rect class="side-tab" x="481" y="48" width="20" height="185" rx="8" fill="var(--panel-grey)"/>

    <g class="brand brand--mirrored" transform="translate(495 0) scale(-1 1)">
      <rect x="56" y="112" width="50" height="50" rx="3" fill="var(--white)"/>
      <text class="wordmark" x="120" y="147" font-size="44" fill="var(--white)">Northgate</text>
      <text class="wordmark" x="122" y="163" font-size="13" letter-spacing="5.2" fill="var(--white)">DEVELOPMENTS</text>
    </g>

    <path class="blank-panel" d="M54 283 L54 218 Q54 200 72 200 L322 200 Q340 200 352 210 L437 283 Z" fill="var(--panel-grey)"/>
  </svg>
</section>

</body>
</html>
```